Single-sided business card for restaurant velmora with new logo made on this site

Business card options with new logo including restaurant name, address, phone number and website. This business card is single-sided only and will be presented at the hostess desk for clients to take. I would like to see options based on a cream card background, a white card background, a yellow card background and a burgundy colored background. It needs to be elegant and traditional.

Target Market(s)

local and international crowd

Industry/Entity Type

restaurant

Contact Information for Business Card

address, website and phone number

Font styles to use
Serif

Colors
EE7325
F08F49
F5BC92
FAE3D3
FDF4ED

Requirements
Must have
• new logo, address, phone number, website
Should not have
• more than three colors

```html
<!DOCTYPE html>
<html lang="es">
<head>
<meta charset="utf-8">
<title>Velmora — Tarjetas de presentación</title>
<link rel="stylesheet" href="https://fonts.googleapis.com/css2?family=Cinzel:wght@400;500&display=swap">
<style>
  :root {
    --backdrop: #dcdcdc;
    --card-white: #f7f7f5;
    --card-white-edge: #ececea;
    --card-yellow: #f1b32d;
    --card-yellow-edge: #e2a42a;
    --gold: #e8b025;
    --brown: #3b1a1a;
  }
  * { margin: 0; padding: 0; box-sizing: border-box; }
  html, body { width: 1200px; height: 960px; overflow: hidden; }
  body {
    background: var(--backdrop);
    position: relative;
    font-family: "Cinzel", "Times New Roman", serif;
    color: var(--brown);
  }
  .card {
    position: absolute;
    top: 126px;
    width: 402px;
    height: 700px;
    border: 13px solid;
  }
  .card--white { left: 166px; background: var(--card-white); border-color: var(--card-white-edge); }
  .card--yellow { left: 643px; background: var(--card-yellow); border-color: var(--card-yellow-edge); }

  .logo-frame {
    position: absolute;
    left: 35px;
    top: 30px;
    width: 306px;
    height: 403px;
    border: 3px solid var(--accent);
  }
  .card--white { --accent: var(--gold); }
  .card--yellow { --accent: var(--brown); }

  .logo-name {
    position: absolute;
    left: 0; right: 0;
    top: 168px;
    text-align: center;
    font-size: 48px;
    font-weight: 400;
    letter-spacing: 6px;
    color: var(--brown);
  }
  .logo-since {
    position: absolute;
    left: 20px; right: 20px;
    top: 252px;
    display: flex;
    align-items: center;
    gap: 12px;
    font-size: 12px;
    color: var(--brown);
    white-space: nowrap;
  }
  .logo-since::before, .logo-since::after {
    content: "";
    flex: 1;
    height: 2px;
    background: var(--accent);
    border-radius: 2px;
  }

  .contact {
    position: absolute;
    left: 0; right: 0;
    text-align: center;
    font-size: 17px;
    letter-spacing: 0.5px;
    line-height: 20px;
  }
  .contact--address { top: 497px; }
  .contact--phone { top: 576px; font-size: 18px; letter-spacing: 1px; }
  .contact--web { top: 612px; font-size: 16px; letter-spacing: 1px; }
</style>
</head>
<body>
  <article class="card card--white">
    <div class="logo-frame">
      <div class="logo-name">VELMORA</div>
      <div class="logo-since">Desde 1999</div>
    </div>
    <p class="contact contact--address">Camelia 415<br>Bahías de Huatulco<br>Oaxaca, Mexico CP 70989</p>
    <p class="contact contact--phone">Reservaciones · 958-555-0142</p>
    <p class="contact contact--web">www.velmora.com.mx</p>
  </article>

  <article class="card card--yellow">
    <div class="logo-frame">
      <div class="logo-name">VELMORA</div>
      <div class="logo-since">Desde 1999</div>
    </div>
    <p class="contact contact--address">Camelia 415<br>Bahías de Huatulco<br>Oaxaca, Mexico CP 70989</p>
    <p class="contact contact--phone">Reservaciones · 958-555-0142</p>
    <p class="contact contact--web">www.velmora.com.mx</p>
  </article>
</body>
</html>
```